Marcus Delbridge Finance

Need a personal website advertising Equipment Finance,Business Finance,Commercial Finance, Construction Finance, Bridging Finance. Similar websites are www.corvalend.com.au / www.tarmivest.com.au / www.qbr7.com.au /wwwhalvecredit.com.au

Target Market(s)

Business People

Industry/Entity Type

Business

Number of Pages Required

3 page

Font styles to use
Serif
Sans Serif

Requirements
Must have
• All i want is a simple corporate looking website advertising Equipment Finance, Commercial Finance, Construction Finance, Business Finance, Bridging Finance,

```html
<!DOCTYPE html>
<html lang="en">
<head>
<meta charset="utf-8">
<title>Marcus Delbridge Finance</title>
<link rel="stylesheet" href="https://fonts.googleapis.com/css2?family=Lora:wght@400;700&family=Open+Sans:wght@400;600&display=swap">
<style>
:root{
  --ink:#1c2757;
  --nav:#2f3c91;
  --nav-active:#1b2563;
  --text:#666;
  --white:#fff;
  --tile-dark:#262626;
  --panel:#f1f1f1;
  --serif:'Lora',Georgia,serif;
  --sans:'Open Sans',Arial,sans-serif;
}
*{box-sizing:border-box;margin:0;padding:0}
html,body{width:782px;height:1200px;overflow:hidden;background:var(--white)}
body{position:relative;font-family:var(--sans);color:var(--text)}

.site-header{position:absolute;top:0;left:0;width:782px;height:63px}
.brand{position:absolute;left:86px;top:16px;font-family:var(--serif);font-size:20.5px;color:var(--ink);font-weight:400}
.header-phone{position:absolute;right:87px;top:24px;font-family:var(--sans);font-size:11px;color:var(--ink);display:flex;align-items:center;gap:5px}

.main-nav{position:absolute;top:63px;left:0;width:782px;height:26px;background:var(--nav)}
.main-nav ul{list-style:none;position:absolute;left:86px;top:0;height:26px;display:flex}
.main-nav li{font-family:var(--serif);font-size:8px;color:#c9cde8;height:26px;line-height:26px;padding:0 12.5px}
.main-nav li.active{background:var(--nav-active);color:var(--white);font-weight:700}

.hero{position:absolute;top:89px;left:0;width:782px;height:310px;
  background:
    radial-gradient(ellipse 70px 50px at 590px 60px,rgba(255,250,235,.75),rgba(255,250,235,0) 100%),
    radial-gradient(ellipse 190px 210px at 560px 150px,#b9bcc4 0%,#9a9ca4 45%,rgba(90,88,86,0) 100%),
    linear-gradient(100deg,#262321 0%,#3a3431 30%,#4b4540 55%,#3b3632 80%,#2c2826 100%)}
.hero-title{position:absolute;left:87px;top:106px;font-family:var(--serif);font-size:21px;line-height:28px;color:var(--white);font-weight:400}
.hero-btn{position:absolute;left:88px;top:172px;width:72px;height:25px;background:var(--white);font-family:var(--serif);font-weight:700;font-size:7.5px;color:var(--ink);text-align:center;line-height:25px}
.hero-arrow{position:absolute;top:148px}

.welcome-title{position:absolute;left:86px;top:446px;font-family:var(--serif);font-size:22px;color:var(--ink);font-weight:400}
.welcome-text{position:absolute;left:86px;top:480px;width:425px;font-size:7.6px;line-height:14.5px;color:var(--text);text-align:justify}
.read-more{position:absolute;left:86px;top:597px;width:64px;height:23px;border:1px solid #bbb;font-size:7.5px;line-height:21px;text-align:center;color:#555}
.welcome-media{position:absolute;left:534px;top:452px;width:161px;height:168px;border:3px solid #777;
  background:
    radial-gradient(ellipse 60px 40px at 110px 50px,rgba(220,220,220,.35),rgba(220,220,220,0)),
    radial-gradient(ellipse 55px 40px at 50px 115px,rgba(40,60,90,.7),rgba(40,60,90,0)),
    linear-gradient(170deg,#4d4d4d 0%,#3c3c3c 50%,#2a2a2a 100%)}

.services{position:absolute;left:86px;top:672px;width:609px;height:292px;display:grid;grid-template-columns:203px 203px 203px;grid-template-rows:146px 146px}
.service{display:flex;align-items:center;justify-content:center;text-align:center;font-family:var(--serif);font-weight:700;font-size:11px;line-height:13.5px;color:var(--white);text-transform:uppercase}
.s1{background:radial-gradient(ellipse 120px 60px at 110px 120px,#4a5a9a,rgba(74,90,154,0)),linear-gradient(180deg,#2a3d84 0%,#34478c 55%,#4a5894 100%)}
.s2{background:radial-gradient(ellipse 90px 50px at 100px 100px,#8793bf,rgba(135,147,191,0)),linear-gradient(180deg,#5362a0 0%,#4e5e9c 100%)}
.s3{background:radial-gradient(ellipse 80px 70px at 180px 60px,#3f5196,rgba(63,81,150,0)),linear-gradient(160deg,#1f3275,#1b2b6a)}
.s4{background:radial-gradient(ellipse 100px 60px at 120px 60px,#34488a,rgba(52,72,138,0)),linear-gradient(180deg,#223479 0%,#1b2b69 100%)}
.s5{background:radial-gradient(ellipse 70px 90px at 90px 60px,#3f528f,rgba(63,82,143,0)),linear-gradient(180deg,#2a3c82 0%,#3e5090 100%)}
.s6{background:var(--tile-dark)}

.map{position:absolute;left:86px;top:964px;width:305px;height:156px;
  background:
    linear-gradient(90deg,rgba(0,0,0,0) 0 70%,#cfcfcf 70% 100%),
    radial-gradient(ellipse 30px 22px at 60px 72px,#d0d0d0,rgba(208,208,208,0)),
    linear-gradient(160deg,#e6e6e6,#dadada)}
.contact-panel{position:absolute;left:391px;top:964px;width:304px;height:156px;background:var(--panel)}
.contact-list{list-style:none;position:absolute;left:22px;top:40px}
.contact-list li{display:flex;align-items:center;gap:9px;font-family:var(--serif);font-size:8.3px;color:#333;height:21px}
.contact-list svg{width:7px;height:8px}

.footer-links{position:absolute;left:86px;top:1146px;font-family:var(--serif);font-size:6.6px;color:#444}
.copyright{position:absolute;left:86px;top:1164px;font-family:var(--serif);font-size:6.6px;color:#444}
.social{position:absolute;left:643px;top:1151px;display:flex;gap:4px}
.social span{width:17px;height:17px;border-radius:50%;display:block}
.social .a{background:#3b5697}.social .b{background:#2aa3e0}.social .c{background:#0f76b3}
</style>
</head>
<body>

<header class="site-header">
  <div class="brand">Marcus Delbridge Finance</div>
  <div class="header-phone">
    <svg width="6" height="9" viewBox="0 0 6 9"><rect x="0.6" y="0.6" width="4.8" height="7.8" rx="0.8" fill="none" stroke="#1c2757" stroke-width="1.1"/><rect x="2.2" y="6.6" width="1.6" height="0.9" fill="#1c2757"/></svg>
    61 7 5550 0142
  </div>
</header>

<nav class="main-nav">
  <ul>
    <li class="active">Home</li><li>About</li><li>Equipment Finance</li><li>Business Finance</li><li>Commercial Finance</li><li>Construction Finance</li><li>Bridging Finance</li><li>Contact</li>
  </ul>
</nav>

<section class="hero" role="img" aria-label="Photo of hands pointing at business charts on a tablet">
  <h1 class="hero-title">Duis lobortis eget fringilla<br>sit amet convallis</h1>
  <div class="hero-btn">CONTACT US</div>
  <svg class="hero-arrow" style="left:5px" width="10" height="10" viewBox="0 0 10 10"><path d="M9 5H2M5 1.5 1.5 5 5 8.5" fill="none" stroke="#fff" stroke-width="1.6"/></svg>
  <svg class="hero-arrow" style="left:767px" width="10" height="10" viewBox="0 0 10 10"><path d="M1 5h7M5 1.5 8.5 5 5 8.5" fill="none" stroke="#fff" stroke-width="1.6"/></svg>
</section>

<h2 class="welcome-title">Welcome</h2>
<p class="welcome-text">Mr. Marcus Delbridge serves as Operations Director of Kestrel Financial Services Pty Ltd. Mr. Delbridge has 16 years experience in the Financial Services and bridging Finance industry, both in Australia, as well as in South Africa. He was employed by the South African based business (NORTHVALE FINANCE) for the majority of its operation. He held senior operational positions within Northvale Finance and provided staff support and direction, training and operational control for the Company. Since the establishment of Kestrel Financial Services, Mr. Delbridge has implemented constant Procedures, Policy and system updates to products in order to meet market demands and to minimize risk on Bridging loans originated.</p>
<div class="read-more">Read more</div>
<div class="welcome-media" role="img" aria-label="Laptop in front of a chalk drawing of rising bar charts"></div>

<section class="services">
  <div class="service s1" role="img" aria-label="Drilling machinery on a site, blue tint">Equipment<br>Finance</div>
  <div class="service s2" role="img" aria-label="Glasses on business documents, blue tint">Business<br>Finance</div>
  <div class="service s3" role="img" aria-label="Coins and market figures, blue tint">Commercial<br>Finance</div>
  <div class="service s4" role="img" aria-label="Building interior under construction, blue tint">Construction<br>Finance</div>
  <div class="service s5" role="img" aria-label="Business person and stacked blocks, blue tint">Bridging<br>Finance</div>
  <div class="service s6">Book an<br>Appointment</div>
</section>

<div class="map" role="img" aria-label="Street map showing the office location"></div>
<div class="contact-panel">
  <ul class="contact-list">
    <li><svg viewBox="0 0 7 8"><path d="M3.5 8C1.5 5.3 0.8 4.2 0.8 3.1a2.7 2.7 0 0 1 5.4 0C6.2 4.2 5.5 5.3 3.5 8z" fill="#555"/><circle cx="3.5" cy="3" r="1" fill="#f1f1f1"/></svg>4b 18 Harbour Parade, Coral Bay, Queensland 4217, Australia</li>
    <li><svg viewBox="0 0 7 8"><rect x="1.2" y="0.5" width="4.6" height="7" rx="0.7" fill="none" stroke="#555"/></svg>Phone: 61 7 5550 0142</li>
    <li><svg viewBox="0 0 7 8"><rect x="0.5" y="3" width="6" height="4.5" fill="#555"/><rect x="1.8" y="0.5" width="3.4" height="2.8" fill="none" stroke="#555"/></svg>Fax: 61 7 5550 0198</li>
    <li><svg viewBox="0 0 7 8"><rect x="0.3" y="1.8" width="6.4" height="4.6" fill="#555"/><path d="M0.5 2 3.5 4.5 6.5 2" fill="none" stroke="#f1f1f1" stroke-width="0.7"/></svg>Email : info@marcusdelbridge.com</li>
  </ul>
</div>

<footer>
  <div class="footer-links">Home &nbsp;|&nbsp; About &nbsp;|&nbsp; Equipment Finance &nbsp;|&nbsp; Business Finance &nbsp;|&nbsp; Commercial Finance &nbsp;|&nbsp; Construction Finance &nbsp;|&nbsp; Bridging Finance &nbsp;|&nbsp; Contact</div>
  <div class="copyright">Copyright &nbsp;©&nbsp; 2017 &nbsp; Company name. &nbsp; All rights reserved.</div>
  <div class="social"><span class="a"></span><span class="b"></span><span class="c"></span></div>
</footer>

</body>
</html>
```